Budget Brand Responsive Website

Flat vector style website needed for value based IT support company. looking for clean, illustration intensive based design. Current test site can be found at www.bright-mend.co.uk and holding page it www.brightmend.co.uk this will show text and services, please feel free to use placeholder text if you think we need alternative text in places. Emphasis should be on low cost support and services listed on the site, would be nice to see costs in bold images. important colors are the blue, orange and white, see holding page and attached image of an advert

It Company

```html
<!DOCTYPE html>
<html lang="en">
<head>
<meta charset="utf-8">
<title>Bright Mend – Managed Service Provider</title>
<link href="https://fonts.googleapis.com/css2?family=Open+Sans:wght@400;600;700;800&display=swap" rel="stylesheet">
<style>
:root{
  --blue:#1f5fa8;
  --blue-dark:#163f73;
  --orange:#e8782a;
  --orange-dark:#c85f17;
  --white:#ffffff;
  --grey:#eef0f3;
  --grey-mid:#d9dde3;
  --text:#4a4f57;
}
*{box-sizing:border-box;margin:0;padding:0}
html,body{width:773px;height:1200px;overflow:hidden}
body{font-family:"Open Sans",sans-serif;color:var(--text);background:var(--white)}
.site-header{height:36px;display:flex;align-items:center;justify-content:space-between;padding:0 26px}
.brand{font-weight:700;font-size:17px;color:var(--blue-dark)}
.main-nav{display:flex;gap:22px;font-size:8px;font-weight:700;color:var(--blue-dark);align-items:center}
.main-nav a.active{color:var(--orange)}
.hero{position:relative;height:340px;overflow:hidden}
.hero-visual{position:absolute;inset:0;background:radial-gradient(circle at 55% 60%,#4f8fcf 0%,#23578f 40%,#0f2f57 100%)}
.hero-copy{position:absolute;left:0;right:0;top:140px;text-align:center;color:var(--white)}
.hero-copy h1{font-size:27px;font-weight:700;letter-spacing:.5px;text-shadow:0 1px 3px rgba(0,0,0,.4)}
.hero-copy p{font-size:10px;font-weight:600;margin-top:4px;letter-spacing:.4px}
.btn{display:inline-block;background:var(--orange);color:var(--white);font-size:7px;font-weight:700;padding:5px 14px;border-radius:2px;letter-spacing:.4px}
.hero-copy .btn{margin-top:12px}
.hero-arrow{position:absolute;top:160px;width:22px;height:22px}
.hero-arrow.left{left:10px}.hero-arrow.right{right:10px}
.services{height:170px;background:var(--orange);display:grid;grid-template-columns:repeat(6,1fr);padding:20px 40px 0}
.service{text-align:center;color:var(--white)}
.service-icon{width:52px;height:52px;border-radius:50%;background:var(--orange-dark);margin:0 auto 14px;display:flex;align-items:center;justify-content:center}
.service h3{font-size:10px;font-weight:800;letter-spacing:.5px;margin-bottom:5px}
.service p{font-size:6.5px;line-height:1.55}
.about{height:220px;display:flex;padding:32px 60px 0 26px;gap:30px}
.about-text{flex:1}
.about h2{font-size:15px;font-weight:800;color:var(--blue-dark);margin-bottom:10px}
.about p{font-size:7px;line-height:1.6;margin-bottom:14px}
.about-visual{width:250px;height:150px;border-radius:4px;background:linear-gradient(160deg,#dfe6ee,#9fb0c2)}
.pricing{height:270px;background:var(--grey);padding:24px 64px 0}
.pricing h2{text-align:center;font-size:13px;font-weight:800;color:var(--blue-dark);margin-bottom:16px}
.price-grid{display:grid;grid-template-columns:repeat(4,1fr);gap:18px}
.price-card{background:var(--white);border:1px solid var(--grey-mid);height:170px}
.price-card header{background:var(--blue);color:var(--white);text-align:center;padding:6px 4px 5px}
.price-card header small{display:block;font-size:5.5px;font-weight:600}
.price-card header strong{font-size:9px;font-weight:800}
.price-card .tagline{background:var(--grey-mid);text-align:center;font-size:5.5px;font-weight:700;padding:4px 6px;color:var(--blue-dark)}
.price-card ul{list-style:none;padding:8px 10px}
.price-card li{display:flex;justify-content:space-between;align-items:center;font-size:6.5px;padding:5px 0;border-bottom:1px solid var(--grey)}
.price-card li b{color:var(--orange);font-size:11px;font-weight:800}
.price-card.cloud li{justify-content:center}
.newsletter{height:80px;background:var(--orange);text-align:center;padding-top:16px}
.newsletter h2{font-size:13px;font-weight:800;color:var(--white);margin-bottom:10px;letter-spacing:.5px}
.newsletter .form{display:flex;justify-content:center;gap:10px}
.newsletter .field{width:165px;height:16px;background:var(--white);font-size:6px;text-align:left;padding:4px 6px;color:#8a9099}
.newsletter .btn{background:var(--blue);padding:4px 12px}
.site-footer{height:84px;background:var(--blue-dark);color:var(--white);display:flex;justify-content:space-between;padding:18px 26px 0}
.site-footer nav{font-size:6.5px}
.site-footer small{display:block;font-size:5.5px;margin-top:8px;opacity:.8}
.social{display:flex;gap:6px}
.social span{width:16px;height:16px;background:var(--white);opacity:.9}
</style>
</head>
<body>
<header class="site-header">
  <div class="brand">Bright Mend</div>
  <nav class="main-nav">
    <a class="active">HOME</a><a>SUPPORT</a><a>SERVICES</a><a>ABOUT</a><a>CONTACT</a>
    <svg width="9" height="9" viewBox="0 0 10 10"><circle cx="4" cy="4" r="3" fill="none" stroke="#163f73" stroke-width="1.4"/><line x1="6.2" y1="6.2" x2="9.3" y2="9.3" stroke="#163f73" stroke-width="1.4"/></svg>
  </nav>
</header>

<section class="hero">
  <div class="hero-visual" role="img" aria-label="Hand touching a glowing network of technology icons on a blue background"></div>
  <svg class="hero-arrow left" viewBox="0 0 20 20"><polyline points="13,3 6,10 13,17" fill="none" stroke="#fff" stroke-width="2.5"/></svg>
  <svg class="hero-arrow right" viewBox="0 0 20 20"><polyline points="7,3 14,10 7,17" fill="none" stroke="#fff" stroke-width="2.5"/></svg>
  <div class="hero-copy">
    <h1>MANAGED SERVICE PROVIDER (MSP)</h1>
    <p>OUR COMMITMENT TO DELIVERING LEADING TECHNOLOGIES COMBINED WITH A FOCUS ON QUALITY SERVICE</p>
    <span class="btn">GET MORE INFORMATION</span>
  </div>
</section>

<section class="services">
  <div class="service">
    <div class="service-icon"><svg width="26" height="26" viewBox="0 0 24 24" fill="none" stroke="#fff" stroke-width="2"><path d="M4 14v-2a8 8 0 0116 0v2"/><rect x="3" y="13" width="4" height="6" rx="1" fill="#fff"/><rect x="17" y="13" width="4" height="6" rx="1" fill="#fff"/></svg></div>
    <h3>SUPPORT</h3><p>Unlimited Remote Support<br>Monitoring and Alerting<br>On-Site Visits Available</p>
  </div>
  <div class="service">
    <div class="service-icon"><svg width="24" height="24" viewBox="0 0 24 24"><path d="M6 3l3 0 2 5-2 1.5a11 11 0 005.5 5.5L16 13l5 2v3a2 2 0 01-2 2A16 16 0 014 5a2 2 0 012-2z" fill="#fff"/></svg></div>
    <h3>VOICE</h3><p>VoIP Telephone Systems<br>Telephone Lines<br>SIP Trunking and Calls</p>
  </div>
  <div class="service">
    <div class="service-icon"><svg width="26" height="26" viewBox="0 0 24 24" fill="none" stroke="#fff" stroke-width="1.8"><circle cx="12" cy="12" r="9"/><ellipse cx="12" cy="12" rx="4" ry="9"/><line x1="3" y1="12" x2="21" y2="12"/></svg></div>
    <h3>INTERNET</h3><p>Business Broadband<br>Leased Lines<br>Fibre Connectivity</p>
  </div>
  <div class="service">
    <div class="service-icon"><svg width="24" height="24" viewBox="0 0 24 24"><rect x="5" y="11" width="14" height="10" rx="1.5" fill="#fff"/><path d="M8 11V8a4 4 0 018 0v3" fill="none" stroke="#fff" stroke-width="2"/></svg></div>
    <h3>SECURITY</h3><p>Encryption<br>Antivirus and Firewall<br>Patch Management</p>
  </div>
  <div class="service">
    <div class="service-icon"><svg width="24" height="24" viewBox="0 0 24 24" fill="#fff"><rect x="4" y="3" width="16" height="5" rx="1"/><rect x="4" y="10" width="16" height="5" rx="1"/><rect x="4" y="17" width="16" height="5" rx="1"/></svg></div>
    <h3>HOSTING</h3><p>Hosted Mailbox<br>CloudDesk Suite<br>Email Security</p>
  </div>
  <div class="service">
    <div class="service-icon"><svg width="28" height="28" viewBox="0 0 24 24"><path d="M7 18a4 4 0 01-.5-8A5.5 5.5 0 0117 9a4.5 4.5 0 01.5 9z" fill="#fff"/></svg></div>
    <h3>CLOUD</h3><p>Backup and DR<br>Virtual Desktops<br>Private Cloud Servers</p>
  </div>
</section>

<section class="about">
  <div class="about-text">
    <h2>ABOUT BRIGHT MEND</h2>
    <p>Bright Mend is a trusted, value-led Managed Service Provider with many years of industry experience. Our commitment to delivering leading technologies combined with a focus on quality service means we make the most of your IT while keeping costs low and predictable. We have a portfolio of support services and products designed to suit the needs of any size of business.</p>
    <span class="btn">READ MORE</span>
  </div>
  <div class="about-visual" role="img" aria-label="Computer monitor showing a figure climbing steps beside a chalkboard"></div>
</section>

<section class="pricing">
  <h2>PRICING FOR OUR MOST POPULAR SERVICES</h2>
  <div class="price-grid">
    <article class="price-card">
      <header><small>UNLIMITED REMOTE SUPPORT</small><strong>SUPPORT</strong></header>
      <div class="tagline">UNLIMITED REMOTE SUPPORT</div>
      <ul><li>Workstations<b>£9.50</b></li><li>Cloud VM<b>£20.00</b></li><li>Servers<b>£45.00</b></li></ul>
    </article>
    <article class="price-card">
      <header><small>VOICE</small><strong>VOICE</strong></header>
      <div class="tagline">LOWER RATES AND CHARGES</div>
      <ul><li>Fibre Line<b>£45.00</b></li><li>Line Rental<b>£11.00</b></li><li>Phone numbers<b>£5.00</b></li></ul>
    </article>
    <article class="price-card">
      <header><small>HOSTING</small><strong>HOSTING</strong></header>
      <div class="tagline">FLEXIBLE AND SECURE</div>
      <ul><li>Email hosting from<b>£2.00</b></li><li>Email protection<b>£1.00</b></li><li>CloudDesk from<b>£3.16</b></li></ul>
    </article>
    <article class="price-card cloud">
      <header><small>CLOUD</small><strong>CLOUD</strong></header>
      <div class="tagline">REDUCE COSTS AND INCREASE PERFORMANCE</div>
      <ul><li>Online Backup</li><li>Private Cloud Server</li><li>Virtual Desktop</li></ul>
    </article>
  </div>
</section>

<section class="newsletter">
  <h2>NEWSLETTER SUBSCRIPTION</h2>
  <div class="form"><span class="field">NAME</span><span class="field">EMAIL</span><span class="field">MESSAGE</span><span class="btn">SEND MESSAGE</span></div>
</section>

<footer class="site-footer">
  <div>
    <nav>Home &nbsp;|&nbsp; Support &nbsp;|&nbsp; Services &nbsp;|&nbsp; About &nbsp;|&nbsp; Contact</nav>
    <small>© 2016 www.bright-mend.co.uk – All rights reserved</small>
  </div>
  <div class="social"><span></span><span></span><span></span></div>
</footer>
</body>
</html>
```